Business Card for a mobile physiotherapy company

I need a layout for a business card for a mobile physiotherapy company.
Slogan is "Mobile Physiotherapy - Your Road To Recovery"
Phone number is 867-555-0142
Email VardenTherapy@postnest.ca (subject to change with website)
Website www.VardenTherapy.ca
My name and credentials: Luke Varden Luke Varden, BSc(kin), MPT, CAFCI, IMS
Information maybe included: Direct Billing, Services including Physiotherapy, IMS, acupuncture
Maybe include facebook and instagram logos
One side with the logo clean and sharp
Other side with details, try not to look too busy, keep everything concise

```html
<!DOCTYPE html>
<html lang="en">
<head>
<meta charset="utf-8">
<title>Varden Therapy – Business Card</title>
<link rel="stylesheet" href="https://fonts.googleapis.com/css2?family=Lato:wght@400;700&family=Tinos:wght@400;700&display=swap">
<style>
  :root {
    --backdrop: #666666;
    --card-white: #ffffff;
    --brand-green: #0f4f46;
    --brand-navy: #1f3a66;
    --text-dark: #333333;
    --back-teal: #13504f;
    --back-blue: #274a74;
    --rule: rgba(255, 255, 255, 0.35);
    --white: #ffffff;
  }
  * { margin: 0; padding: 0; box-sizing: border-box; }
  html, body { width: 1200px; height: 900px; overflow: hidden; }
  body { background: var(--backdrop); position: relative; font-family: "Lato", sans-serif; }

  .card {
    position: absolute;
    top: 275px;
    width: 477px;
    height: 294px;
    box-shadow: 2px 3px 4px rgba(0, 0, 0, 0.45);
  }
  .card-front {
    left: 120px;
    background: var(--card-white);
    border-radius: 0 62px 0 62px;
  }
  .card-back {
    left: 620px;
    background: linear-gradient(30deg, var(--back-teal) 0%, #1a4e60 50%, var(--back-blue) 100%);
    border-radius: 58px 0 58px 0;
    color: var(--white);
  }

  /* Front */
  .brand-name {
    position: absolute;
    left: 36px;
    top: 133px;
    width: 184px;
    text-align: center;
    font-family: "Lato", sans-serif;
    font-weight: 700;
    font-size: 21px;
    line-height: 26px;
    color: var(--brand-navy);
  }

  .divider {
    position: absolute;
    left: 238px;
    top: 95px;
    width: 1px;
    height: 103px;
    background: #dddddd;
  }
  .person { position: absolute; left: 260px; top: 93px; }
  .person-name {
    font-family: "Tinos", serif;
    font-weight: 700;
    font-size: 17px;
    color: var(--brand-green);
    letter-spacing: 0.5px;
    line-height: 20px;
  }
  .person-credentials {
    font-family: "Tinos", serif;
    font-size: 13px;
    color: var(--brand-navy);
    line-height: 18px;
  }
  .contact-list { list-style: none; margin-top: 15px; }
  .contact-item {
    display: flex;
    align-items: center;
    gap: 4px;
    font-size: 14px;
    color: var(--text-dark);
    line-height: 17.5px;
  }
  .contact-icon { width: 11px; height: 11px; fill: var(--brand-green); flex: none; }

  /* Back */
  .services {
    position: absolute;
    top: 99px;
    left: 0;
    width: 100%;
    text-align: center;
    list-style: none;
    font-size: 14px;
    line-height: 25.5px;
    text-transform: uppercase;
    letter-spacing: 0.2px;
  }
  .social-row {
    position: absolute;
    left: 72px;
    top: 200px;
    width: 331px;
    height: 22px;
  }
  .social-row::before {
    content: "";
    position: absolute;
    left: 0; right: 0; top: 10px;
    height: 1px;
    background: var(--rule);
  }
  .social-dot {
    position: absolute;
    top: 1px;
    width: 20px;
    height: 20px;
    border-radius: 50%;
    background: var(--white);
  }
  .social-dot.first { left: 143px; }
  .social-dot.second { left: 168px; }
  .slogan {
    position: absolute;
    top: 242px;
    left: 0;
    width: 100%;
    text-align: center;
    font-family: "Tinos", serif;
    font-size: 14px;
    text-transform: uppercase;
    letter-spacing: 0.2px;
  }
</style>
</head>
<body>
  <section class="card card-front">
    <p class="brand-name">Varden Therapy</p>
    <div class="divider"></div>
    <div class="person">
      <p class="person-name">LUKE VARDEN,</p>
      <p class="person-credentials">BSC(KIN), MPT, CAFCI, IMS</p>
      <ul class="contact-list">
        <li class="contact-item">
          <svg class="contact-icon" viewBox="0 0 12 12" aria-hidden="true"><path d="M1 4c2-3 8-3 10 0l-2 1.5-1-1.5H4L3 5.5z M3 6h6l1 4H2z"/></svg>
          867-555-0142
        </li>
        <li class="contact-item">
          <svg class="contact-icon" viewBox="0 0 12 12" aria-hidden="true"><path d="M1 3h10v7H1z" /><path d="M1 3l5 4 5-4" fill="none" stroke="#fff" stroke-width="1"/></svg>
          VardenTherapy@postnest.ca
        </li>
        <li class="contact-item">
          <svg class="contact-icon" viewBox="0 0 12 12" aria-hidden="true"><circle cx="6" cy="6" r="5"/></svg>
          www.VardenTherapy.ca
        </li>
      </ul>
    </div>
  </section>

  <section class="card card-back">
    <ul class="services">
      <li>Direct Billing</li>
      <li>Service Including Physiotherapy</li>
      <li>IMS &nbsp;|&nbsp; Acupuncture</li>
    </ul>
    <div class="social-row">
      <span class="social-dot first"></span>
      <span class="social-dot second"></span>
    </div>
    <p class="slogan">Mobile Physiotherapy - Your Road To Recovery</p>
  </section>
</body>
</html>
```